Business Card Design

Business Card for professional consulting firm working with large financial institutions.

Target Market(s)

Executive buyers

Industry/Entity Type

Banking

Contact Information for Business Card

Mild creativity wanted. Not boring, but do elaborate artwork.

Font styles to use
Serif
Sans Serif

Colors

Designer to choose colors to be used in the design.

Requirements
Must have
• Standard business card features - company name, individual name, telephone, website, email, locations.
Nice to have
• Two colors
Should not have
• too many colors, fancy printing, cartoons.

```html
<!DOCTYPE html>
<html lang="en">
<head>
<meta charset="utf-8">
<title>k7advisory business card</title>
<link rel="stylesheet" href="https://fonts.googleapis.com/css2?family=Quicksand:wght@500;700&display=swap">
<style>
  :root {
    --stage: #e8e5e0;
    --card-white: #ffffff;
    --card-grey: #d9d9d9;
    --swoosh-grey: #c4c4c4;
    --ink: #2b2b2b;
    --ink-soft: #9a9a9a;
    --card-black: #050505;
    --brand-white: #f5f5f5;
  }
  * { box-sizing: border-box; margin: 0; padding: 0; }
  html, body {
    width: 1200px; height: 950px; overflow: hidden;
    background: var(--stage);
  }
  .stage { position: relative; width: 1200px; height: 950px; }
  .card {
    position: absolute; top: 155px;
    width: 380px; height: 640px;
    box-shadow: 0 10px 30px rgba(0,0,0,0.18);
    overflow: hidden;
  }
  .card-front { left: 185px; background: var(--card-white); }
  .card-back  { left: 635px; background: var(--card-black); }

  .front-backdrop { position: absolute; inset: 0; width: 100%; height: 100%; }

  .contact-stack {
    position: absolute; left: 0; right: 0; top: 175px;
    display: flex; flex-direction: column; align-items: center;
    font-family: "Quicksand", sans-serif; color: var(--ink);
    text-align: center;
  }
  .icon { width: 14px; height: 14px; fill: var(--ink); display: block; }
  .person-name { margin-top: 6px; font-weight: 700; font-size: 22px; letter-spacing: 0.5px; }
  .person-title { font-weight: 700; font-size: 15px; color: var(--ink-soft); letter-spacing: 0.5px; }
  .icon-gap { margin-top: 16px; }
  .contact-line { font-weight: 700; font-size: 14px; line-height: 1.3; margin-top: 6px; }

  .brand {
    position: absolute; left: 50%; top: 50%;
    transform: translate(-50%, -50%);
    display: flex; align-items: center; gap: 12px;
  }
  .brand-name {
    font-family: "Quicksand", sans-serif; font-weight: 700;
    font-size: 34px; color: var(--brand-white); white-space: nowrap;
  }
  .brand-dot {
    width: 12px; height: 12px; border-radius: 50%; background: var(--brand-white);
  }
</style>
</head>
<body>
<main class="stage">

  <section class="card card-front" aria-label="Business card front">
    <svg class="front-backdrop" viewBox="0 0 380 640" preserveAspectRatio="none" aria-hidden="true">
      <rect width="380" height="640" fill="var(--card-grey)"/>
      <ellipse cx="175" cy="330" rx="270" ry="290" fill="var(--swoosh-grey)"/>
      <ellipse cx="185" cy="325" rx="262" ry="282" fill="var(--card-white)"/>
    </svg>

    <div class="contact-stack">
      <svg class="icon" viewBox="0 0 14 14" aria-hidden="true">
        <circle cx="7" cy="4" r="3.2"/><path d="M1 14c0-4 2.7-6 6-6s6 2 6 6z"/>
      </svg>
      <p class="person-name">DANIEL REEVE</p>
      <p class="person-title">CEO/FOUNDER</p>

      <svg class="icon icon-gap" viewBox="0 0 14 14" aria-hidden="true">
        <path d="M7 0a4.8 4.8 0 0 0-4.8 4.8C2.2 8.5 7 14 7 14s4.8-5.5 4.8-9.2A4.8 4.8 0 0 0 7 0zm0 6.8a2 2 0 1 1 0-4 2 2 0 0 1 0 4z"/>
      </svg>
      <p class="contact-line">4120 Harbor Street<br>Fairbanks, Alaska 34580</p>

      <svg class="icon icon-gap" viewBox="0 0 14 14" aria-hidden="true">
        <path d="M3 0.5l2.2 3-1.3 1.6c.8 1.8 2.2 3.2 4 4l1.6-1.3 3 2.2-1.2 2.6C6.4 12.6 1.4 7.6 0.4 2z"/>
      </svg>
      <p class="contact-line">555 210 4417</p>

      <svg class="icon icon-gap" viewBox="0 0 14 14" aria-hidden="true">
        <path d="M0 3h14v8H0z"/>
        <path d="M0.8 3.6l6.2 4.5 6.2-4.5" stroke="#fff" stroke-width="1" fill="none"/>
      </svg>
      <p class="contact-line">info@k7advisory.com</p>

      <svg class="icon icon-gap" viewBox="0 0 14 14" aria-hidden="true">
        <circle cx="7" cy="7" r="6.5"/>
        <path d="M0.5 7h13M7 0.5c-2.5 3-2.5 10 0 13M7 0.5c2.5 3 2.5 10 0 13" stroke="#fff" stroke-width="0.9" fill="none"/>
      </svg>
      <p class="contact-line">www.k7advisory.com</p>
    </div>
  </section>

  <section class="card card-back" aria-label="Business card back">
    <div class="brand">
      <span class="brand-dot" aria-hidden="true"></span>
      <span class="brand-name">k7advisory</span>
    </div>
  </section>

</main>
</body>
</html>
```